Business card design for Automotive workshop

We need a business card for a new automotive repair and tyre shop called Keelstone Prime Automotive located in New Zealand. We are a clean, modern and fresh workshop and company.

Front needs to feature logo,
my name:
Marlo Fenwicke (director)

Address:
48 Tarn Lane
Whitianga 3510

Phone: 07 594 2713
Mobile: 027 451 9362
Email: office@keelstoneautomotive.example.nz
Website: keelstoneautomotive.example.nz

Back needs to feature an area to write down appointment details, date and time.

Also feature a list of jobs and work we do such as,
Vehicle Servicing
All Mechanical Repairs
Warrant of Fitness
Tyres & Wheel Alignments
Automotive Diagnostics
Automotive Parts & Supplies

```html
<!DOCTYPE html>
<html lang="en">
<head>
<meta charset="utf-8">
<title>Keelstone Prime Automotive – Business Card</title>
<link rel="stylesheet" href="https://fonts.googleapis.com/css2?family=Arimo:wght@400;700&family=Lato:wght@400;700&display=swap">
<style>
  :root {
    --backdrop: #e4e4e6;
    --card: #ffffff;
    --brand-red: #e31b23;
    --ink: #1c1c1c;
    --ink-soft: #3a3a3a;
    --rule: #b9b9b9;
  }
  * { box-sizing: border-box; margin: 0; padding: 0; }
  html, body { width: 1200px; height: 900px; overflow: hidden; }
  body {
    background: var(--backdrop);
    position: relative;
    font-family: "Arimo", Arial, sans-serif;
    color: var(--ink);
  }
  .card {
    position: absolute;
    width: 580px;
    height: 350px;
    background: var(--card);
    border-radius: 28px;
    box-shadow: 0 6px 18px rgba(0,0,0,0.12);
  }
  .card--back { left: 90px; top: 70px; }
  .card--front { left: 530px; top: 480px; }

  .brand {
    display: flex;
    align-items: center;
    gap: 10px;
    font-family: "Arimo", Arial, sans-serif;
    font-weight: 700;
    color: var(--brand-red);
    text-transform: uppercase;
    letter-spacing: 1px;
    white-space: nowrap;
  }
  .brand__mark {
    width: 16px; height: 16px;
    background: var(--brand-red);
    flex: none;
  }

  /* Back */
  .card--back .brand {
    position: absolute; left: 0; right: 0; top: 52px;
    justify-content: center;
    font-size: 28px;
  }
  .services {
    position: absolute; left: 30px; right: 30px; top: 118px;
    text-align: center;
    font-family: "Lato", sans-serif;
    font-size: 16px;
    line-height: 24px;
    color: var(--ink-soft);
    list-style: none;
  }
  .services__dot {
    display: inline-block;
    width: 7px; height: 7px;
    border-radius: 50%;
    background: var(--brand-red);
    margin: 0 6px 2px;
    vertical-align: middle;
  }
  .appointment {
    position: absolute; left: 60px; right: 60px; top: 210px;
  }
  .appointment__title {
    text-align: center;
    font-family: "Lato", sans-serif;
    font-weight: 700;
    font-size: 19px;
    letter-spacing: 0.5px;
    margin-bottom: 30px;
  }
  .appointment__fields { display: flex; gap: 28px; }
  .field {
    flex: 1;
    display: flex; align-items: flex-end; gap: 10px;
    font-size: 17px; letter-spacing: 0.5px;
  }
  .field__line { flex: 1; border-bottom: 1px solid var(--rule); height: 1px; margin-bottom: 4px; }

  /* Front */
  .card--front .brand {
    position: absolute; left: 42px; top: 56px;
    font-size: 23px;
  }
  .address {
    position: absolute; right: 36px; top: 104px;
    font-size: 17px; line-height: 21px;
    font-style: normal;
    text-align: left;
  }
  .person { position: absolute; left: 42px; top: 180px; }
  .person__name {
    color: var(--brand-red);
    font-weight: 700;
    font-size: 20px;
    letter-spacing: 0.5px;
    text-transform: uppercase;
  }
  .person__role { font-size: 16px; margin-top: 1px; }
  .contacts {
    position: absolute; left: 42px; top: 240px;
    list-style: none;
    font-size: 16px; line-height: 22px;
  }
  .contacts__item { display: flex; align-items: center; gap: 8px; }
  .contacts__icon { width: 13px; height: 13px; fill: var(--brand-red); flex: none; }
</style>
</head>
<body>

<section class="card card--back" aria-label="Card back">
  <div class="brand"><span class="brand__mark"></span>Keelstone Prime Automotive</div>
  <ul class="services">
    <li>Vehicle Servicing<span class="services__dot"></span>All Mechanical Repairs<span class="services__dot"></span>Warrant of Fitness</li>
    <li>Tyres &amp; Wheel Alignments<span class="services__dot"></span>Automotive Diagnostics</li>
    <li>Automotive Parts &amp; Supplies</li>
  </ul>
  <div class="appointment">
    <h2 class="appointment__title">NEXT APPOINTMENT</h2>
    <div class="appointment__fields">
      <div class="field"><span>DATE</span><span class="field__line"></span></div>
      <div class="field"><span>TIME</span><span class="field__line"></span></div>
    </div>
  </div>
</section>

<section class="card card--front" aria-label="Card front">
  <div class="brand"><span class="brand__mark"></span>Keelstone Prime Automotive</div>
  <address class="address">48 Tarn Lane<br>Whitianga 3510</address>
  <div class="person">
    <div class="person__name">Marlo Fenwicke</div>
    <div class="person__role">Director</div>
  </div>
  <ul class="contacts">
    <li class="contacts__item">
      <svg class="contacts__icon" viewBox="0 0 16 16" aria-hidden="true"><path d="M3 1h3l1.5 4-2 1.5a9 9 0 0 0 4 4L11 8.5 15 10v3a2 2 0 0 1-2 2C6.4 15 1 9.6 1 3a2 2 0 0 1 2-2z"/></svg>
      07 594 2713</li>
    <li class="contacts__item">
      <svg class="contacts__icon" viewBox="0 0 16 16" aria-hidden="true"><path d="M4 0h8a1 1 0 0 1 1 1v14a1 1 0 0 1-1 1H4a1 1 0 0 1-1-1V1a1 1 0 0 1 1-1zm1 2v10h6V2zm3 11a1 1 0 1 0 0 2 1 1 0 0 0 0-2z"/></svg>
      027 451 9362</li>
    <li class="contacts__item">
      <svg class="contacts__icon" viewBox="0 0 16 16" aria-hidden="true"><path d="M1 3h14v10H1zm1.5 1.5L8 9l5.5-4.5v-.1h-11z"/></svg>
      office@keelstoneautomotive.example.nz</li>
    <li class="contacts__item">
      <svg class="contacts__icon" viewBox="0 0 16 16" aria-hidden="true"><circle cx="8" cy="8" r="7"/><path d="M1 8h14M8 1c-3 3-3 11 0 14M8 1c3 3 3 11 0 14" stroke="#fff" stroke-width="1.2" fill="none"/></svg>
      keelstoneautomotive.example.nz</li>
  </ul>
</section>

</body>
</html>
```